Boutique Real Estate Brokerage Tessly Realty Website Design

Winning designer work on migrate as well through nest ferry.
We need a new website as an informational hub to aid our print and digital strategy as well as showing that we are located in Brooklyn and Florida. I have a boutique real estate brokerage and advisory firm specializing in residential leasing, multifamily sales and 1031 Exchange appropriation. This won't be a portal to search properties, it will be a place for information. I'd like space for an ebook to be downloaded and information on my probate sales and multifamily leasing marketing campaigns. I included my logo and will leave it up to the designer to come up with colors to match it. I have also attached verbiage for each page. The final design should have a modern high end look that reflects gentrifying Brooklyn as well as beautiful Florida.
Thank you!
Target Market(s)
Owners of income producing real estate and develop-able land in Brooklyn, NY and Florida.
Industry/Entity Type
Real Estate
Coding
Coded - Design and coding required
Number of Pages Required
5+ page
Colors
Designer to choose colors to be used in the design.
Requirements
Must have
- A modern elegant look
Nice to have
- pictures of brooklyn and florida
Should not have
- real estate search pages

```html
<!DOCTYPE html>
<html lang="en">
<head>
<meta charset="utf-8">
<title>Tessly Realty</title>
<link rel="stylesheet" href="https://fonts.googleapis.com/css2?family=Montserrat:wght@400;600;700&family=Lato:wght@300;400&display=swap">
<style>
:root{
  --ink:#000;
  --ink-soft:#1a1a1a;
  --heading:#4a4a4a;
  --heading-light:#9a9a9a;
  --text:#666;
  --line:#cfcfcf;
  --grey-bg:#efefef;
  --white:#fff;
  --hero-top:#4b6278;
  --hero-mid:#8c7a66;
  --hero-low:#2a3a48;
  --band-a:#2c2218;
  --band-b:#4a3a2a;
}
*{margin:0;padding:0;box-sizing:border-box}
html,body{width:1200px;height:3057px;overflow:hidden;background:var(--white)}
body{position:relative;font-family:"Lato",sans-serif;color:var(--text)}
.abs{position:absolute}
.btn{position:absolute;display:flex;align-items:center;justify-content:center;background:var(--ink);color:var(--white);font-family:"Montserrat",sans-serif;font-weight:600;font-size:18px;border-radius:5px}
.grad-heading{font-family:"Montserrat",sans-serif;font-weight:700;background:linear-gradient(90deg,var(--heading) 0%,var(--heading) 25%,var(--heading-light) 45%,var(--heading-light) 60%,var(--heading) 80%);-webkit-background-clip:text;background-clip:text;color:transparent}

/* header */
.site-header{left:0;top:0;width:1200px;height:94px;background:var(--ink)}
.brand{left:78px;top:0;height:94px;display:flex;align-items:center;gap:12px;color:#cfcfcf;font-family:"Montserrat",sans-serif;font-weight:700;font-size:15px;letter-spacing:2px;text-transform:uppercase}
.brand-mark{width:44px;height:44px;border-radius:50%;background:#8a8a8a}
.nav a{position:absolute;color:#ddd;font-family:"Lato",sans-serif;font-size:14px;letter-spacing:.5px;text-decoration:none;top:38px}
.nav .active{left:663px;top:26px;width:83px;height:42px;border:1px solid #fff;border-radius:4px;display:flex;align-items:center;justify-content:center;color:#fff}

/* hero */
.hero{left:0;top:94px;width:1200px;height:562px;background:linear-gradient(180deg,var(--hero-top) 0%,#7f8c96 22%,var(--hero-mid) 40%,#4c5c50 55%,var(--hero-low) 70%,#1e2a36 100%)}
.hero-title{left:0;top:318px;width:1200px;text-align:center;color:var(--white);font-family:"Montserrat",sans-serif;font-weight:700;font-size:36px;line-height:47px;letter-spacing:.5px;text-shadow:0 2px 6px rgba(0,0,0,.5)}
.wave{left:0;top:640px}

/* services */
.services{left:0;top:656px;width:1200px;height:714px;background:var(--grey-bg)}
.section-title{left:0;width:1200px;text-align:center;font-size:42px}
.card{position:absolute;top:833px;width:313px;height:469px;background:var(--white)}
.card-photo{height:218px}
.card h3{position:absolute;left:27px;top:249px;font-family:"Montserrat",sans-serif;font-weight:600;font-size:18px;color:#222}
.card p{position:absolute;left:27px;top:287px;width:265px;font-size:13.5px;line-height:26px;color:var(--text)}
.card .btn{left:29px;top:386px;width:161px;height:52px}

/* about */
.about-kicker{left:122px;top:1446px;font-size:20px}
.about-title{left:120px;top:1478px;font-size:41px}
.about-copy{left:122px;width:420px;font-size:13.5px;line-height:27px}
.about-photo{left:620px;top:1440px;width:540px;height:471px;background:radial-gradient(ellipse at 40% 45%,#b9b6b2 0%,#d9d8d6 45%,#fff 75%)}

/* call band */
.call-band{left:0;top:1911px;width:1200px;height:261px;background:linear-gradient(135deg,var(--band-a),var(--band-b) 50%,#1e1812)}
.call-text{left:0;top:1986px;width:1200px;text-align:center;color:var(--white);font-family:"Montserrat",sans-serif;font-weight:600;font-size:28px}
.phone-btn{left:473px;top:2047px;width:254px;height:59px;border:1.5px solid #fff;border-radius:7px;display:flex;align-items:center;justify-content:center;gap:14px;color:#fff;font-family:"Montserrat",sans-serif;font-weight:600;font-size:25px}

/* contact */
.contact-sub{left:0;top:2288px;width:1200px;text-align:center;font-size:15px;color:#666}
.field{left:327px;width:546px;border-bottom:1px solid var(--line);font-size:13px;color:#666;padding-left:2px}

/* footer */
.site-footer{left:0;top:2725px;width:1200px;height:332px;background:linear-gradient(135deg,#0d0d0d,#000 40%,#111 70%,#000)}
.footer-brand{left:0;top:2810px;width:1200px;display:flex;justify-content:center;align-items:center;gap:12px;color:#cfcfcf;font-family:"Montserrat",sans-serif;font-weight:700;font-size:22px;letter-spacing:2px;text-transform:uppercase}
.social{position:absolute;top:2898px;width:46px;height:46px;border:1.5px solid #fff;border-radius:50%}
.footer-links{left:0;top:2963px;width:1200px;text-align:center;color:#bbb;font-size:14px}
.copyright{left:0;top:2988px;width:1200px;text-align:center;color:#999;font-size:13px}
.copyright b{color:#fff;font-weight:700}
</style>
</head>
<body>

<header class="abs site-header">
  <div class="abs brand"><span class="brand-mark"></span>Tessly Realty</div>
  <nav class="nav">
    <a class="active" href="#">HOME</a>
    <a href="#" style="left:779px">ABOUT US</a>
    <a href="#" style="left:884px">SERVICES</a>
    <a href="#" style="left:982px">CONTACT US</a>
    <svg class="abs" style="left:1107px;top:39px" width="15" height="15" viewBox="0 0 15 15"><circle cx="6" cy="6" r="4.5" fill="none" stroke="#fff" stroke-width="2"/><line x1="9.5" y1="9.5" x2="14" y2="14" stroke="#fff" stroke-width="2.4"/></svg>
  </nav>
</header>

<section class="abs hero" role="img" aria-label="Waterfront apartment buildings with palm trees and a fountain on a lake"></section>
<h1 class="abs hero-title">ASSISTING LANDLORDS INCREASE PROFITS<br>WHILE DECREASING THE STRESS.</h1>
<a class="btn" style="left:503px;top:435px;width:193px;height:57px;font-size:20px">CONTACT US</a>

<section class="abs services"></section>
<svg class="abs wave" width="1200" height="62" viewBox="0 0 1200 62">
  <path d="M0 16 H505 C545 16 560 59 600 59 C640 59 655 16 695 16 H1200 V62 H0Z" fill="#efefef"/>
  <path d="M0 16 H505 C545 16 560 59 600 59 C640 59 655 16 695 16 H1200 V0 H0Z" fill="#1e2a36"/>
  <g fill="#fff">
    <circle cx="579" cy="11" r="1"/><circle cx="584" cy="11" r="1"/><circle cx="589" cy="11" r="1"/><circle cx="594" cy="11" r="1"/><circle cx="599" cy="11" r="1"/><circle cx="604" cy="11" r="1"/><circle cx="609" cy="11" r="1"/><circle cx="614" cy="11" r="1"/><circle cx="619" cy="11" r="1"/>
    <circle cx="584" cy="16" r="1"/><circle cx="589" cy="16" r="1"/><circle cx="594" cy="16" r="1"/><circle cx="599" cy="16" r="1"/><circle cx="604" cy="16" r="1"/><circle cx="609" cy="16" r="1"/><circle cx="614" cy="16" r="1"/>
    <circle cx="589" cy="21" r="1" fill="#888"/><circle cx="594" cy="21" r="1" fill="#888"/><circle cx="599" cy="21" r="1" fill="#888"/><circle cx="604" cy="21" r="1" fill="#888"/><circle cx="609" cy="21" r="1" fill="#888"/>
    <circle cx="594" cy="26" r="1" fill="#888"/><circle cx="599" cy="26" r="1" fill="#888"/><circle cx="604" cy="26" r="1" fill="#888"/>
    <circle cx="599" cy="31" r="1" fill="#888"/>
  </g>
</svg>

<h2 class="abs section-title grad-heading" style="top:754px">HOW WE CAN HELP</h2>

<article class="card" style="left:97px">
  <div class="card-photo" role="img" aria-label="Bright apartment kitchen and dining room interior" style="background:linear-gradient(180deg,#c9c6c0,#a8a296 60%,#8a7a62)"></div>
  <h3>MULTI-FAMILY LEASING</h3>
  <p>We specialize in sourcing quality tenants for landlords with high income, good credit and no evictions.</p>
  <a class="btn">LEARN MORE</a>
</article>
<article class="card" style="left:443px">
  <div class="card-photo" role="img" aria-label="Brick apartment building facade with fire escapes" style="background:linear-gradient(180deg,#8a8a84,#a49a8c 45%,#5e564c)"></div>
  <h3 style="left:25px">MULTIFAMILY SALES</h3>
  <p style="left:26px">Tessly Realty provides clients with reliable real estate research, advisory and transaction services.</p>
  <a class="btn" style="left:27px">LEARN MORE</a>
</article>
<article class="card" style="left:789px">
  <div class="card-photo" role="img" aria-label="Aerial view of Florida land and a lake" style="background:linear-gradient(180deg,#aab2b8 0%,#8c9488 30%,#6a7458 60%,#34403c 100%)"></div>
  <h3 style="left:30px">SITE SELECTION ADVISORS</h3>
  <p style="left:31px">Our industry best Commercial Real Estate site selection services assists developers in narrow.</p>
  <a class="btn" style="left:32px">LEARN MORE</a>
</article>

<p class="abs about-kicker grad-heading">WELCOME TO</p>
<h2 class="abs about-title grad-heading">TESSLY REALTY</h2>
<p class="abs about-copy" style="top:1545px">Tessly Realty NYC•PB is a full-service real estate brokerage firm with offices located in Brooklyn, New York and West Palm Beach, Florida. Our firm focuses on multifamily leasing, sales and Commercial Real Estate Site Selection Advisory</p>
<p class="abs about-copy" style="top:1669px">Our clients are private and institutional multifamily real estate investors.Our team differentiates ourselves by our ability to investigate the highest and best use for real estate assets as well as our high deal closing rate.</p>
<a class="btn" style="left:123px;top:1797px;width:161px;height:52px">LEARN MORE</a>
<div class="abs about-photo" role="img" aria-label="Smiling real estate agent beside a white architectural city model"></div>

<section class="abs call-band" role="img" aria-label="Brooklyn brownstone entrance at night"></section>
<p class="abs call-text">If You have an an Any Question For Contact Us On</p>
<div class="abs phone-btn">
  <svg width="28" height="28" viewBox="0 0 28 28"><circle cx="14" cy="14" r="12.5" fill="none" stroke="#fff" stroke-width="1.6"/><path d="M10 8 C8 11 9 16 12 19 C14 21 16 21 18 20 L16.5 17 L15 17.8 C13.3 16.6 12 14.6 11.8 12.6 L13.2 11.7 Z" fill="#fff"/></svg>
  <span>123 456 7890</span>
</div>

<h2 class="abs section-title grad-heading" style="top:2227px">CONTACT US</h2>
<p class="abs contact-sub">If you want more info or just to say hello !</p>
<div class="abs field" style="top:2353px;height:25px">Name *</div>
<div class="abs field" style="top:2403px;height:30px">Email *</div>
<div class="abs field" style="top:2460px;height:29px">Phone *</div>
<div class="abs field" style="top:2512px;height:81px">Message *</div>
<a class="btn" style="left:527px;top:2608px;width:146px;height:52px">SUBMIT</a>

<footer class="abs site-footer"></footer>
<div class="abs footer-brand"><span class="brand-mark" style="width:52px;height:52px"></span>Tessly Realty</div>
<span class="social" style="left:525px" aria-label="Social profile one"></span>
<span class="social" style="left:577px" aria-label="Social profile two"></span>
<span class="social" style="left:631px" aria-label="Social profile three"></span>
<p class="abs footer-links">Home &nbsp;|&nbsp; About Us | &nbsp;Services &nbsp;|&nbsp; Contact Us</p>
<p class="abs copyright">©<b>TESSLY REALTY</b> - 2019 All Right Reserved.</p>

</body>
</html>
```